Detail Shop Business card design

i need a business card design for my new detailing company called 'Brisk's Polish Works'. i want an all black and white design . simple, direct and to the point. i want the designer to choose a fitting font to match the logothe front should have logo, address, phone and email and the back side should have a slogan and text indicating that we offer services on anything including cars, trucks, motorcycles and RVs. slogan will read "we take pride in your ride"
maybe also very small on the back side the IG icon with Brisks_Polish_Works

phone 208.417.6352
address 3847 E Larkin Ave
Marlow OR 97214
email: BrisksPolish@mailvexo.com

Target Market(s)

all ages , auto enthusiasts

Industry/Entity Type

Automotive

Contact Information for Business Card

the front should have logo, address, phone and email and the back side should have a slogan and text indicating that we offer services on anything including cars, trucks, motorcycles and RVs. slogan will read "we take pride in your ride"

phone 208.417.6352
address 3847 E Larkin Ave
Marlow OR 97214

Colors
000000
ffffff

Requirements
Must have
• bold font and very simple design with good spacing
Nice to have
• anything creative from the designer indicating we service any types of vehicles
Should not have
• any colors ,

```html
<!DOCTYPE html>
<html lang="en">
<head>
<meta charset="utf-8">
<title>Brisk's Polish Works – Business Card</title>
<link href="https://fonts.googleapis.com/css2?family=Arvo:wght@400;700&display=swap" rel="stylesheet">
<style>
  :root {
    --ink: #000000;
    --paper: #ffffff;
    --backdrop: #d9d9d9;
    --shadow: rgba(0,0,0,0.28);
  }
  * { margin: 0; padding: 0; box-sizing: border-box; }
  html, body {
    width: 1200px; height: 835px; overflow: hidden;
    background: var(--backdrop);
    font-family: "Arvo", Georgia, serif;
    color: var(--ink);
  }
  .sheet {
    position: relative; width: 1200px; height: 835px;
    display: flex; align-items: center; justify-content: center; gap: 40px;
  }
  .card {
    position: relative; width: 540px; height: 309px;
    background: var(--paper); overflow: hidden;
    box-shadow: 0 10px 24px var(--shadow);
  }

  /* brand mark: name in text font + one plain circle */
  .brand { display: flex; align-items: center; gap: 10px; }
  .brand-dot {
    width: 34px; height: 34px; border-radius: 50%;
    background: var(--ink); flex: none;
  }
  .brand-name {
    font-weight: 700; font-size: 21px; line-height: 1.1;
    text-transform: uppercase; letter-spacing: 0.5px;
  }

  /* contact card */
  .card-contact .brand { position: absolute; left: 28px; top: 30px; width: 200px; }
  .card-contact .pitch { position: absolute; left: 250px; top: 34px; width: 270px; }
  .slogan {
    font-weight: 700; font-size: 29px; line-height: 1.0;
    text-transform: uppercase; letter-spacing: 0.3px;
  }
  .services { margin-top: 8px; font-size: 12.5px; line-height: 1.3; }
  .contact-band {
    position: absolute; left: 0; right: 0; bottom: 0; height: 120px;
    background: var(--ink); color: var(--paper);
    display: flex; justify-content: space-between; align-items: flex-end;
    padding: 0 28px 22px;
  }
  .contact-list { list-style: none; font-size: 13px; line-height: 1.85; }
  .contact-list li { display: flex; align-items: center; gap: 9px; }
  .contact-list svg, .address svg { width: 13px; height: 13px; fill: var(--paper); flex: none; }
  .ig-mark { width: 13px; text-align: center; font-size: 13px; }
  .address { display: flex; gap: 9px; font-size: 13px; line-height: 1.4; align-items: flex-start; }
  .address svg { margin-top: 3px; }

  /* back card */
  .card-back .swoosh { position: absolute; inset: 0; width: 100%; height: 100%; }
  .card-back .center {
    position: absolute; inset: 0;
    display: flex; flex-direction: column; align-items: center; justify-content: center; gap: 12px;
  }
  .card-back .brand-name { font-size: 24px; }
  .tagline { font-weight: 700; font-size: 14px; text-transform: uppercase; letter-spacing: 0.6px; }
</style>
</head>
<body>
<main class="sheet">

  <section class="card card-contact" aria-label="Card front">
    <div class="brand">
      <span class="brand-dot"></span>
      <span class="brand-name">Brisk's Polish Works</span>
    </div>
    <div class="pitch">
      <h1 class="slogan">We take pride in your ride</h1>
      <p class="services">We offer services on anything including cars, trucks, motorcycles and RVs.</p>
    </div>
    <div class="contact-band">
      <ul class="contact-list">
        <li><svg viewBox="0 0 24 24"><path d="M6.6 10.8c1.4 2.8 3.8 5.1 6.6 6.6l2.2-2.2c.3-.3.7-.4 1-.2 1.1.4 2.3.6 3.6.6.6 0 1 .4 1 1V20c0 .6-.4 1-1 1C10.6 21 3 13.4 3 4c0-.6.4-1 1-1h3.5c.6 0 1 .4 1 1 0 1.3.2 2.5.6 3.6.1.3 0 .7-.2 1z"/></svg>208.417.6352</li>
        <li><svg viewBox="0 0 24 24"><path d="M2 5h20v14H2z M4 7v.4l8 5.3 8-5.3V7z" fill-rule="evenodd"/></svg>BrisksPolish@mailvexo.com</li>
        <li><span class="ig-mark">@</span>Brisks_Polish_Works</li>
      </ul>
      <div class="address">
        <svg viewBox="0 0 24 24"><path d="M12 2a7 7 0 0 0-7 7c0 5.2 7 13 7 13s7-7.8 7-13a7 7 0 0 0-7-7zm0 9.5A2.5 2.5 0 1 1 12 6.5a2.5 2.5 0 0 1 0 5z"/></svg>
        <p>3847 E Larkin Ave<br>Marlow OR 97214</p>
      </div>
    </div>
  </section>

  <section class="card card-back" aria-label="Card back">
    <svg class="swoosh" viewBox="0 0 540 309" preserveAspectRatio="none" aria-hidden="true">
      <path d="M0 0 H150 C110 40 60 50 0 70 Z" fill="#000"/>
      <path d="M540 309 H360 C420 260 480 200 540 110 Z" fill="#000"/>
    </svg>
    <div class="center">
      <div class="brand">
        <span class="brand-dot"></span>
        <span class="brand-name">Brisk's Polish Works</span>
      </div>
      <p class="tagline">We take pride in your ride</p>
    </div>
  </section>

</main>
</body>
</html>
```